San Francisco Leading Consulting firm - 47Vora Web Design Project

•Create a Web Design
•Uncoded webpage layout design
•2 Pages Design - Homepage + Interior Page

Task Description
Hello, we're looking for a re-design our current website www.47vora-example.com

we have a sample mockup design @

http://47vora.pubtrellis-example.org/

This shows the layout that we like and also a sample of 6 pictures that would change based on where you mouse over..

6 pictures HOME design needs to be included.

SMART
THOUGHTFUL
FLEXIBLE
CREATIVE SERVICES
TECHNICAL SERVICES
PARTNERS

sites we like:

http://www.melvanadvisory-example.com/Home.cfm?id=Home
http://www.plinthworks-example.com/index.html

Our company can be best described as: 100+ employees, cutting-edge, depandable, innovative, strong, smart.

Our Primary focus is: IT Consulting Services and Creative Design services

47Vora LLC is a consulting firm providing creative design, business and technology solutions to both private and public interests.

Established in 1996, 47Vora is a San Francisco based company providing specialists for a range of business needs including:

Creative Design Services
•Print
•Logo Design
•Website Design
•Illustration

and

Business and Technology solutions

•Application Software and Web Development
•Business Process Re-Design (BPR)
•Business/Systems Analysis and Requirement Documentation
•Mentoring and Training
•Network/Hardware Installation Services
•System Design and Architecture
•Vendor Management
•Docuvault Architecture and Implementation

our sample mockup site:

Reason: Due to holiday season, we're not available to work with designers and finilize our design.  

Thank you very much for submitting your design.

We appreciate your time and creativity.   Since, our office is currently closed for holidays, we will be reviewing it in details next week and will make our decision as soon as possible.

It would be great if you could submit any of your changes by Wed next week, so it would be part of our reviews. 

Please see updated wireframe under attachments:  we have some minor updates to our wireframe that we would like you to update your designs, if possible.  

We also encorouge you not to use our standard wireframe and come up with more unique designs.   Everything would be considered when we review your design.

 

Target Market(s)

Creative services and professional services clients, including government agencies

Industry/Entity Type

Business

Requirements
Must have
• Clean, professional look, easy navigation

```html
<!DOCTYPE html>
<html lang="en">
<head>
<meta charset="utf-8">
<title>47Vora LLC — Business, Technology & Creative Design</title>
<link rel="stylesheet" href="https://fonts.googleapis.com/css2?family=Arimo:wght@400;700&family=PT+Sans+Narrow:wght@400;700&family=Lobster&display=swap">
<style>
  :root {
    --brand-blue: #0083b8;
    --button-blue: #48a9dc;
    --link-blue: #1a87c0;
    --footer-blue: #5cc3f0;
    --ink: #2b2b2b;
    --grey: #9a9a9a;
    --nav-grey: #8c8c8c;
    --orange: #f7931e;
    --green: #8dc21f;
    --bulb-blue: #8fd3f7;
    --footer-bg: #2d2d2d;
    --white: #ffffff;
  }
  * { margin: 0; padding: 0; box-sizing: border-box; }
  html, body { width: 1200px; height: 900px; overflow: hidden; background: var(--white); }
  body { position: relative; font-family: "Arimo", Arial, sans-serif; color: var(--ink); }
  .abs { position: absolute; }

  .brand { left: 152px; top: 40px; display: flex; align-items: center; gap: 10px;
    font-size: 28px; color: var(--ink); letter-spacing: 1px; }
  .brand-dot { width: 26px; height: 26px; border-radius: 50%; background: var(--button-blue); }

  .topbar { left: 670px; top: 19px; font-size: 14.5px; color: var(--grey); white-space: nowrap; }
  .topbar .company { color: var(--link-blue); margin-right: 3px; }
  .topbar-divider { left: 979px; top: 0; width: 1px; height: 38px; background: #cfcfcf; }
  .topbar-contact { left: 992px; top: 19px; font-size: 14.5px; color: var(--link-blue); }

  .main-nav { left: 518px; top: 77px; display: flex; gap: 32px; list-style: none;
    font-family: "PT Sans Narrow", sans-serif; font-size: 17px; color: var(--nav-grey); letter-spacing: .3px; }

  .hero-title { left: 400px; width: 412px; top: 142px; text-align: center;
    font-family: "PT Sans Narrow", sans-serif; font-weight: 700; font-size: 41px; color: var(--ink); line-height: 44px; }

  .hero-visual { left: 460px; top: 190px; width: 282px; height: 198px; border-radius: 90px 90px 24px 24px;
    background: radial-gradient(ellipse at 50% 42%, #2d2d2d 0 38%, var(--bulb-blue) 58%, #d9f0fc 100%); }

  .script { font-family: "Lobster", cursive; font-size: 23px; }
  .big { font-family: "PT Sans Narrow", sans-serif; font-weight: 700; font-size: 50px; line-height: 36px;
    color: var(--ink); }
  .sub { font-family: "PT Sans Narrow", sans-serif; font-weight: 700; font-size: 31px; line-height: 34px; }
  .service-list { list-style: none; font-size: 14.5px; line-height: 24px; color: var(--grey); }

  .left-label { left: 149px; top: 196px; color: var(--orange); }
  .left-title { left: 149px; top: 231px; }
  .left-title span { display: block; padding-left: 13px; }
  .left-sub { left: 170px; top: 305px; color: var(--orange); }
  .left-list { left: 148px; top: 342px; }

  .right-label { left: 832px; top: 196px; color: var(--green); }
  .right-title { left: 832px; top: 231px; width: 243px; }
  .right-title span { display: block; text-align: right; }
  .right-sub { left: 924px; top: 305px; color: var(--green); }
  .right-list { left: 840px; top: 339px; }

  .feature-band { left: 0; top: 481px; width: 1200px; height: 41px; background: var(--brand-blue); }
  .feature-heading { top: 490px; font-family: "PT Sans Narrow", sans-serif; font-weight: 700;
    font-size: 21px; line-height: 26px; color: var(--white); }
  .feature-text { top: 540px; width: 310px; font-size: 14.5px; line-height: 24px; color: #111; }
  .learn-more { top: 625px; font-size: 14.5px; font-weight: 700; color: #111; }
  .learn-button { top: 645px; width: 78px; height: 26px; background: var(--button-blue); }

  .site-footer { left: 0; top: 671px; width: 1200px; height: 229px; background: var(--footer-bg); }
  .footer-link { top: 685px; font-size: 12px; color: var(--white); }
  .copyright { left: 122px; top: 719px; font-size: 12px; color: #e6e6e6; }
  .footer-address { left: 898px; top: 686px; font-size: 13.5px; line-height: 20px; color: var(--white); font-style: normal; }
  .footer-address .company { color: var(--footer-blue); }
</style>
</head>
<body>
  <div class="abs brand"><span class="brand-dot"></span>47Vora</div>

  <div class="abs topbar"><span class="company">47Vora LLC</span> San Francisco, CA 415-555-0148</div>
  <div class="abs topbar-divider"></div>
  <div class="abs topbar-contact">Contact Us</div>

  <ul class="abs main-nav">
    <li>HOME</li><li>COMPANY</li><li>TECHNICAL SERVICES</li><li>CREATIVE SERVICES</li><li>PARTNERS</li>
  </ul>

  <h1 class="abs hero-title">WE BRIDGE THE GAP</h1>
  <div class="abs hero-visual" role="img" aria-label="Two light bulbs side by side, a left brain in orange and a right brain in green"></div>

  <div class="abs script left-label">Left Brain</div>
  <div class="abs big left-title">BUSINESS &amp;<span>TECHNOLOGY</span></div>
  <div class="abs sub left-sub">Solutions</div>
  <ul class="abs service-list left-list">
    <li>• Application Software and Web Development</li>
    <li>• Business Process Re-Design (BPR)</li>
    <li>• Business/Systems Analysis</li>
    <li>• Mentoring and Training</li>
    <li>... and more</li>
  </ul>

  <div class="abs script right-label">Right Brain</div>
  <div class="abs big right-title">CREATIVE<span>DESIGN</span></div>
  <div class="abs sub right-sub">Services</div>
  <ul class="abs service-list right-list">
    <li>• Print and Package Design</li>
    <li>• Brand and Identity Creation</li>
    <li>• User Experience Design</li>
    <li>• Illustration</li>
    <li>... and more</li>
  </ul>

  <div class="abs feature-band"></div>
  <h2 class="abs feature-heading" style="left:122px">For Graphic Designers</h2>
  <h2 class="abs feature-heading" style="left:450px">The 47Vora Difference</h2>
  <h2 class="abs feature-heading" style="left:781px">Team Up With the Best</h2>

  <p class="abs feature-text" style="left:124px;width:300px">We are looking for top creative talent to deliver graphic design solutions for some leading global brands Do you have what it takes?</p>
  <p class="abs feature-text" style="left:451px">Find out why leading corporations and government agencies turn to 47vora to manage their most demanding IT challenges.</p>
  <p class="abs feature-text" style="left:782px;width:305px">When it comes to technology partnerships, our mission it so make you a success. We view our partners as an important part of our team.</p>

  <div class="abs learn-more" style="left:123px">Learn More</div>
  <div class="abs learn-more" style="left:451px">Learn More</div>
  <div class="abs learn-more" style="left:782px">Learn More</div>
  <div class="abs learn-button" style="left:123px"></div>
  <div class="abs learn-button" style="left:450px"></div>
  <div class="abs learn-button" style="left:778px"></div>

  <footer class="abs site-footer"></footer>
  <nav>
    <span class="abs footer-link" style="left:125px">Home</span>
    <span class="abs footer-link" style="left:182px">Company</span>
    <span class="abs footer-link" style="left:259px">Technical Services</span>
    <span class="abs footer-link" style="left:386px">Creative Services</span>
    <span class="abs footer-link" style="left:506px">Partners</span>
    <span class="abs footer-link" style="left:579px">Contact Us</span>
  </nav>
  <div class="abs copyright">Copyright 2010 47Vora LLC. All rights reserved.</div>
  <address class="abs footer-address">
    <span class="company">47Vora LLC</span><br>
    820 Larkin Row, Suite 410<br>
    San Francisco, CA 94109
  </address>
</body>
</html>
```